Private Investigation Business Card Design

I need a business card for a new private investigation company named Brisk Inquiries. I perform mainly surveillance jobs, vehicle repossessions, document serves etc. The final design should aim for a professional look. The logo has a magnifying glass with stick man arms and legs and is in a running action to show the "Brisk" aspect of the name. If the colour scheme could remain the same as the website www.briskinquiries-demo.com.au with silvers,blacks and a couple electric blue highlights.
Industry/Entity Type
Business
Contact Information for Business Card
Morgan Kellaway
Brisk Inquiries
0487316204
PO Box 58, Carnwell NSW 2291
info@briskinquiries-demo.com.au
www.briskinquiries-demo.com.au
Look and feel

```html
<!DOCTYPE html>
<html lang="en">
<head>
<meta charset="utf-8">
<title>Brisk Inquiries – Business Card</title>
<link href="https://fonts.googleapis.com/css2?family=Arimo:wght@400;700&display=swap" rel="stylesheet">
<style>
  :root {
    --backdrop: #2b2b2d;
    --card-white: #ffffff;
    --card-shade: #e9e9ea;
    --silver-light: #f4f4f5;
    --silver-mid: #d6d6d8;
    --silver-dark: #b9b9bc;
    --ink: #1c1c1e;
    --ink-soft: #4a4a4d;
    --mark: #5a5a5e;
  }
  * { box-sizing: border-box; margin: 0; padding: 0; }
  html, body { width: 1200px; height: 871px; overflow: hidden; }
  body {
    background: var(--backdrop);
    font-family: "Arimo", Arial, sans-serif;
    color: var(--ink);
    position: relative;
  }
  .card {
    position: absolute;
    width: 540px;
    height: 330px;
    left: 330px;
    border-radius: 2px;
    box-shadow: 0 10px 30px rgba(0,0,0,.45);
    overflow: hidden;
  }
  .card--back {
    top: 85px;
    background: linear-gradient(135deg, var(--silver-mid) 0%, var(--silver-light) 45%, var(--silver-dark) 100%);
  }
  .card--front {
    top: 456px;
    background: linear-gradient(150deg, var(--card-white) 55%, var(--card-shade) 100%);
  }
  .brand {
    display: flex;
    align-items: center;
    gap: 12px;
    font-weight: 700;
    color: var(--mark);
    letter-spacing: .5px;
    white-space: nowrap;
  }
  .brand__dot {
    width: 22px; height: 22px;
    border-radius: 50%;
    background: var(--mark);
    flex: none;
  }
  .card--back .brand {
    position: absolute;
    left: 95px; top: 112px;
    font-size: 44px;
  }
  .back-web {
    position: absolute;
    left: 95px; top: 200px;
    display: flex; align-items: center; gap: 10px;
    font-size: 14px;
    letter-spacing: 3px;
    color: var(--ink-soft);
  }
  .back-web__rule {
    width: 70px; height: 1px; background: var(--ink-soft);
  }
  .card--front .brand {
    position: absolute;
    left: 36px; top: 30px;
    font-size: 36px;
  }
  .holder {
    position: absolute;
    left: 58px; top: 102px;
  }
  .holder__name {
    font-size: 20px;
    font-weight: 700;
    margin-bottom: 14px;
  }
  .holder__address {
    font-size: 14px;
    line-height: 1.35;
    color: var(--ink-soft);
    margin-bottom: 12px;
  }
  .contact { list-style: none; }
  .contact__item {
    display: flex; align-items: center; gap: 9px;
    font-size: 14.5px;
    line-height: 1.5;
    color: var(--ink);
  }
  .contact__icon { width: 14px; height: 14px; flex: none; fill: var(--ink); }
</style>
</head>
<body>

<section class="card card--back" aria-label="Business card back">
  <div class="brand"><span class="brand__dot"></span>Brisk Inquiries</div>
  <div class="back-web">www.briskinquiries-demo.com.au<span class="back-web__rule"></span></div>
</section>

<section class="card card--front" aria-label="Business card front">
  <div class="brand"><span class="brand__dot"></span>Brisk Inquiries</div>
  <div class="holder">
    <p class="holder__name">Morgan Kellaway</p>
    <p class="holder__address">PO Box 58<br>Carnwell NSW 2291</p>
    <ul class="contact">
      <li class="contact__item">
        <svg class="contact__icon" viewBox="0 0 16 16" aria-hidden="true"><path d="M2 2h4l1.5 3.5-2 1.3a9 9 0 0 0 3.7 3.7l1.3-2L14 10v4c-7 0-12-5-12-12z"/></svg>
        0487 316 204
      </li>
      <li class="contact__item">
        <svg class="contact__icon" viewBox="0 0 16 16" aria-hidden="true"><path d="M1 3h14v10H1z M1.5 3.5 8 9l6.5-5.5" fill="none" stroke="currentColor" stroke-width="1.4"/><rect x="1" y="3" width="14" height="10"/><path d="M1.5 3.8 8 8.8l6.5-5" fill="none" stroke="#fff" stroke-width="1.2"/></svg>
        info@briskinquiries-demo.com.au
      </li>
      <li class="contact__item">
        <svg class="contact__icon" viewBox="0 0 16 16" aria-hidden="true"><circle cx="8" cy="8" r="7"/><path d="M1 8h14M8 1c-3 3.5-3 10.5 0 14M8 1c3 3.5 3 10.5 0 14" fill="none" stroke="#fff" stroke-width="1"/></svg>
        www.briskinquiries-demo.com.au
      </li>
    </ul>
  </div>
</section>

</body>
</html>
```